Business card for Sports Apparel business

DOUBLE SIDED DESIGN
We need business cards for a new sports apparel business. We are developing a protective headband for soccer initially.
Torvalle is focused on designing and developing head protection products to reduce the likelihood of concussion when playing sports. Exploring and understanding medical insights, material science research, current and former players experiences and governing bodies guidelines has allowed Torvalle to develop the safety, style, form and function requirements of a suitable product to bring to market.
Target Market(s)
Mums buying kits for the sons and daughters. Amateur footballers.
Industry/Entity Type
Sporting Good
Contact Information for Business Card
Martin Ashworth - CEO
Mobile: +44 7431589027
Email: martin@torvalle.co.uk
Tel: 0208 5519372
Helena Pargeter - COO
Mob: +44 7385 640117
Email: helena@torvalle.co.uk
Tel: 0208 5519372
Duncan Farrow - CCO
Mob: +44 7564 293081
Email: duncan@torvalle.co.uk
Tel: 0208 5519372
Look and feel
Each slider illustrates characteristics of the customer's brand and the style your logo design should communicate.

```html
<!DOCTYPE html>
<html lang="en">
<head>
<meta charset="utf-8">
<title>Torvalle Business Card</title>
<link rel="stylesheet" href="https://fonts.googleapis.com/css2?family=Montserrat:wght@400;500;700&display=swap">
<style>
  :root {
    --backdrop: #1f2022;
    --brand-blue: #1b5f96;
    --brand-blue-deep: #174f7e;
    --card-white: #ffffff;
    --card-shade: #eeeeee;
    --ink-grey: #555a60;
    --ink-soft: #6b7077;
  }
  * { box-sizing: border-box; margin: 0; padding: 0; }
  html, body { width: 1200px; height: 1021px; overflow: hidden; }
  body {
    background: var(--backdrop);
    font-family: "Montserrat", sans-serif;
    display: flex;
    flex-direction: column;
    align-items: center;
    justify-content: center;
    gap: 56px;
  }
  .card {
    width: 640px;
    height: 366px;
    position: relative;
    box-shadow: 0 10px 28px rgba(0,0,0,0.45);
  }
  .card-back {
    background: var(--brand-blue);
    display: flex;
    align-items: center;
    justify-content: center;
  }
  .back-wordmark {
    font-weight: 500;
    font-size: 58px;
    letter-spacing: 2px;
    color: var(--brand-blue-deep);
    text-transform: uppercase;
  }
  .card-front {
    background: linear-gradient(160deg, var(--card-white) 55%, var(--card-shade) 100%);
  }
  .front-wordmark {
    position: absolute;
    left: 44px;
    top: 40px;
    display: flex;
    align-items: center;
    gap: 12px;
  }
  .wordmark-square {
    width: 22px;
    height: 22px;
    background: var(--brand-blue);
  }
  .wordmark-name {
    font-weight: 500;
    font-size: 40px;
    letter-spacing: 1.5px;
    color: var(--ink-grey);
    text-transform: uppercase;
  }
  .holder {
    position: absolute;
    left: 44px;
    bottom: 88px;
  }
  .holder-name {
    font-weight: 700;
    font-size: 19px;
    color: var(--brand-blue);
  }
  .holder-role {
    font-size: 13px;
    color: var(--ink-soft);
    margin-top: 3px;
  }
  .contact-divider {
    position: absolute;
    left: 350px;
    bottom: 52px;
    width: 2px;
    height: 96px;
    background: var(--brand-blue);
  }
  .contact-list {
    position: absolute;
    left: 376px;
    bottom: 52px;
    list-style: none;
  }
  .contact-list li {
    display: flex;
    align-items: center;
    gap: 8px;
    font-size: 14.5px;
    color: var(--ink-grey);
    line-height: 24px;
  }
  .contact-list svg {
    width: 14px;
    height: 14px;
    flex: none;
  }
</style>
</head>
<body>
  <section class="card card-back" aria-label="Card back">
    <span class="back-wordmark">Torvalle</span>
  </section>

  <section class="card card-front" aria-label="Card front">
    <div class="front-wordmark">
      <span class="wordmark-square"></span>
      <span class="wordmark-name">Torvalle</span>
    </div>

    <div class="holder">
      <p class="holder-name">Martin Ashworth</p>
      <p class="holder-role">CEO</p>
    </div>

    <span class="contact-divider"></span>

    <ul class="contact-list">
      <li>
        <svg viewBox="0 0 14 14" aria-hidden="true"><rect x="3.5" y="1" width="7" height="12" rx="1.2" fill="none" stroke="#1b5f96" stroke-width="1.3"/><line x1="6" y1="11" x2="8" y2="11" stroke="#1b5f96" stroke-width="1.2"/></svg>
        +44 7431589027
      </li>
      <li>
        <svg viewBox="0 0 14 14" aria-hidden="true"><path d="M3 1.5 L5.2 1.5 L6 4.3 L4.6 5.4 C5.4 7.2 6.8 8.6 8.6 9.4 L9.7 8 L12.5 8.8 L12.5 11 C12.5 12 11.6 12.6 10.6 12.4 C6.2 11.6 2.4 7.8 1.6 3.4 C1.4 2.4 2 1.5 3 1.5 Z" fill="#1b5f96"/></svg>
        0208 5519372
      </li>
      <li>
        <svg viewBox="0 0 14 14" aria-hidden="true"><rect x="1" y="3" width="12" height="8.5" fill="none" stroke="#1b5f96" stroke-width="1.3"/><polyline points="1,3 7,8 13,3" fill="none" stroke="#1b5f96" stroke-width="1.3"/></svg>
        martin@torvalle.co.uk
      </li>
      <li>
        <svg viewBox="0 0 14 14" aria-hidden="true"><circle cx="7" cy="7" r="5.8" fill="none" stroke="#1b5f96" stroke-width="1.2"/><ellipse cx="7" cy="7" rx="2.6" ry="5.8" fill="none" stroke="#1b5f96" stroke-width="1"/><line x1="1.2" y1="7" x2="12.8" y2="7" stroke="#1b5f96" stroke-width="1"/></svg>
        www.torvalle.co.uk
      </li>
    </ul>
  </section>
</body>
</html>
```